Calvanto Group Real Estate Company business cards

New business card design, we are generally happy with the basic layout of the existing front of business card, (feel free to change) but require a head shot photo on the back side.

http://www.calvanto.com.au/

Attached logos, and existing business card

------------------------------

Target Market(s)

Real estate

Industry/Entity Type

Real Estate

Contact Information for Business Card

Standard size double sided

Font styles to use
Other font styles liked:
• Futura

Requirements
Must have
• Photo head shot on the back side
Nice to have
• yes
Should not have
• No

```html
<!DOCTYPE html>
<html lang="en">
<head>
<meta charset="utf-8">
<title>Calvanto Group – Business Cards</title>
<link href="https://fonts.googleapis.com/css2?family=Jost:wght@400;500;600&display=swap" rel="stylesheet">
<style>
  :root{
    --orange:#f7941d;
    --purple:#33266e;
    --navy:#2b2466;
    --white:#ffffff;
    --bg:#e9e6e1;
    --photo-a:#3b4560;
    --photo-b:#c9c4bd;
  }
  *{box-sizing:border-box;margin:0;padding:0}
  html,body{width:1200px;height:950px;overflow:hidden}
  body{background:var(--bg);font-family:"Jost",Arial,sans-serif;position:relative}

  .card{position:absolute;width:640px;height:390px;overflow:hidden;
        box-shadow:0 10px 24px rgba(0,0,0,.18)}

  /* Front: orange with headshot */
  .card-front{left:120px;top:60px;background:var(--orange)}
  .headshot{position:absolute;right:60px;top:0;width:250px;height:300px;
            background:linear-gradient(180deg,var(--photo-b) 0%,var(--photo-a) 55%,var(--photo-a) 100%);
            border-radius:120px 120px 0 0}
  .front-brand{position:absolute;left:44px;top:228px}
  .logo-plate{background:var(--white);padding:8px 18px 6px;display:inline-block}
  .brand-name{font-weight:500;color:var(--navy);font-size:44px;line-height:1;letter-spacing:.5px}
  .tagline{font-weight:600;color:var(--navy);font-size:13px;letter-spacing:.5px;margin-top:4px}
  .front-url{color:var(--white);font-size:19px;letter-spacing:2px;margin-top:12px}

  /* Back: white / purple */
  .card-back{left:440px;top:500px;background:var(--white)}
  .back-band{position:absolute;inset:0}
  .back-brand{position:absolute;left:48px;top:70px}
  .back-brand .brand-name{font-size:70px}
  .back-brand .tagline{font-size:16px;margin-top:8px;margin-left:70px}
  .person{position:absolute;right:40px;top:176px;text-align:right}
  .person-name{color:var(--orange);font-weight:600;font-size:22px}
  .person-role{color:var(--white);font-size:16px}
  .contact{position:absolute;left:48px;top:240px;color:var(--white);font-size:16px;line-height:1.45}
  .contact-list{list-style:none;margin-top:6px}
  .contact-list li{display:flex;align-items:center;gap:10px}
  .contact-list svg{width:15px;height:15px;flex:none}
</style>
</head>
<body>

<section class="card card-front">
  <div class="headshot" role="img" aria-label="Head shot photo of the director in a suit and blue tie"></div>
  <div class="front-brand">
    <div class="logo-plate">
      <div class="brand-name">calvanto</div>
      <div class="tagline">Buy &nbsp;|&nbsp; Sell &nbsp;|&nbsp; Rent</div>
    </div>
    <div class="front-url">www.calvanto.com.au</div>
  </div>
</section>

<section class="card card-back">
  <svg class="back-band" viewBox="0 0 640 390" preserveAspectRatio="none" aria-hidden="true">
    <polygon points="0,220 640,150 640,390 0,390" fill="var(--purple)"/>
    <line x1="0" y1="218" x2="640" y2="148" stroke="var(--orange)" stroke-width="3"/>
  </svg>
  <div class="back-brand">
    <div class="brand-name">calvanto</div>
    <div class="tagline">Buy &nbsp;|&nbsp; Sell &nbsp;|&nbsp; Rent</div>
  </div>
  <div class="person">
    <div class="person-name">Daniel Tran</div>
    <div class="person-role">Director</div>
  </div>
  <div class="contact">
    <div>Calvanto Group</div>
    <div>ABN: 12 345 678 901</div>
    <ul class="contact-list">
      <li><svg viewBox="0 0 16 16"><path fill="var(--orange)" d="M3 1h3l1 4-2 1a9 9 0 0 0 5 5l1-2 4 1v3a2 2 0 0 1-2 2A13 13 0 0 1 1 3a2 2 0 0 1 2-2z"/></svg>0400 555 018</li>
      <li><svg viewBox="0 0 16 16"><rect x="1" y="3" width="14" height="10" fill="var(--orange)"/><path d="M1 3l7 6 7-6" fill="none" stroke="var(--purple)" stroke-width="1.4"/></svg>daniel.tran@calvanto.com.au</li>
      <li><svg viewBox="0 0 16 16"><circle cx="8" cy="8" r="7" fill="var(--orange)"/><path d="M1 8h14M8 1c-3 4-3 10 0 14M8 1c3 4 3 10 0 14" fill="none" stroke="var(--purple)" stroke-width="1.2"/></svg>www.calvanto.com.au</li>
    </ul>
  </div>
</section>

</body>
</html>
```